Quorva - corporate Business Card

We need a good look and innovative business card for a new start up company based in Los Angeles called "Quorva". We are in a payment business, including payment card, app, and ewallet. We are expert in online payment and Card not present (CNP) transaction.
We need an innovative, modern business card.

Our logo font is Aero Matics

Target Market(s)

Startup - Bank - Online Payment - Card Manufacturing

Industry/Entity Type

Startup

Contact Information for Business Card

phone: 555 014 7396 - Address: 4172 Marlowe blvd, Dunmere Falls, OR 97418

Requirements
Must have
• Message: innovative, professional, expert, high tech, trust, online payment expert, security
Nice to have
• no comment
Should not have
• no Comment

```html
<!DOCTYPE html>
<html lang="en">
<head>
<meta charset="utf-8">
<title>Quorva – Business Card</title>
<link rel="stylesheet" href="https://fonts.googleapis.com/css2?family=Open+Sans:wght@400;600;700&display=swap">
<style>
  :root {
    --stage: #bdbdbd;
    --paper: #ffffff;
    --brand-red: #c8102e;
    --brand-red-light: #ea3a4d;
    --brand-red-deep: #cf1f35;
    --ink-grey: #6b6b6b;
    --blush: #f7ece8;
  }
  * { box-sizing: border-box; margin: 0; padding: 0; }
  html, body {
    width: 1200px; height: 837px; overflow: hidden;
    background: var(--stage);
    font-family: "Open Sans", Arial, sans-serif;
  }
  .sheet {
    position: relative; width: 1200px; height: 837px;
    display: flex; align-items: center; justify-content: center; gap: 48px;
  }
  .card {
    position: relative; width: 540px; height: 309px; overflow: hidden;
    border-radius: 3px; box-shadow: 0 6px 18px rgba(0,0,0,.18);
  }
  .card-back {
    background: linear-gradient(135deg, var(--brand-red-light), var(--brand-red-deep));
  }
  .card-front { background: var(--paper); }
  .card-front .backdrop-circle {
    position: absolute; left: 40px; top: 120px;
    width: 260px; height: 260px; border-radius: 50%;
    background: var(--blush);
  }
  .contact {
    position: absolute; left: 34px; top: 30px;
  }
  .contact .person-name {
    color: var(--brand-red); font-weight: 700; font-size: 19px; line-height: 1.1;
  }
  .contact .person-role {
    color: var(--ink-grey); font-size: 13px; margin-top: 2px;
  }
  .contact .lines { margin-top: 16px; list-style: none; }
  .contact .lines li {
    display: flex; align-items: center; gap: 7px;
    color: var(--ink-grey); font-size: 13px; line-height: 1.55;
  }
  .contact .icon { width: 13px; height: 13px; flex: none; }
  .brand-lockup {
    position: absolute; right: 40px; top: 112px;
    display: flex; align-items: center; gap: 12px;
  }
  .brand-lockup .brand-dot {
    width: 56px; height: 56px; border-radius: 50%; background: var(--brand-red);
  }
  .brand-lockup .brand-name {
    color: var(--brand-red); font-weight: 600; font-size: 48px; line-height: 1;
    letter-spacing: 1px;
  }
  .address {
    position: absolute; right: 34px; bottom: 26px;
    color: var(--ink-grey); font-size: 13px; line-height: 1.4; text-align: right;
    font-style: normal;
  }
</style>
</head>
<body>
<main class="sheet">
  <section class="card card-back" role="img" aria-label="Back of card: red surface covered with a tonal geometric pattern"></section>

  <section class="card card-front">
    <div class="backdrop-circle" aria-hidden="true"></div>

    <div class="contact">
      <p class="person-name">Dana Whitlow</p>
      <p class="person-role">Managing Director</p>
      <ul class="lines">
        <li>
          <svg class="icon" viewBox="0 0 16 16" aria-hidden="true"><circle cx="8" cy="8" r="8" fill="#c8102e"/><path d="M5 4.5h1.6l.7 1.8-.9.7a5 5 0 0 0 2.6 2.6l.7-.9 1.8.7v1.6c0 .3-.3.6-.6.6A6.5 6.5 0 0 1 4.4 5.1c0-.3.3-.6.6-.6z" fill="#fff"/></svg>
          555 014 7396
        </li>
        <li>
          <svg class="icon" viewBox="0 0 16 16" aria-hidden="true"><circle cx="8" cy="8" r="8" fill="#c8102e"/><rect x="4" y="5" width="8" height="6" fill="none" stroke="#fff" stroke-width="1.1"/><path d="M4 5l4 3.3L12 5" fill="none" stroke="#fff" stroke-width="1.1"/></svg>
          hello@quorvapay.co
        </li>
      </ul>
    </div>

    <div class="brand-lockup">
      <span class="brand-dot" aria-hidden="true"></span>
      <span class="brand-name">quorva</span>
    </div>

    <address class="address">
      4172 Marlowe blvd,<br>Dunmere Falls, OR 97418
    </address>
  </section>
</main>
</body>
</html>
```